Business Card Design

Attached is my current Business card I do not like it but I must save the logo portion of it. Don't like the color or the lettering am looking for more architectural look in grays or taupe with the green more of a charturese color and the blue a charcoal color on a textured paper that looks more like something high-end that would appeal to an architect or a designer. We make concrete decorative items such as concrete fireplaces, sinks, tops and more.

Target Market(s)

Architects designers of Commercial and Residential - artistic features

Industry/Entity Type

Architect

Contact Information for Business Card

Marisol T. Quenby President and Marketing Director
602-418-5093
email marisol@vantorelstone.example
Showroom "Quillmont Design Center" 4183 W Palomar Scottsdale AZ
Fax: 602-731-6624

Font styles to use
Sans Serif

Requirements
Must have
• Architectural
Natural and earthy colors with a touch of color in the existing attached

```html
<!DOCTYPE html>
<html lang="en">
<head>
<meta charset="utf-8">
<title>Vantorel Stone – Business Card</title>
<link rel="stylesheet" href="https://fonts.googleapis.com/css2?family=Ubuntu:wght@300;400&display=swap">
<style>
  :root {
    --charcoal: #1f2937;
    --charcoal-soft: #263242;
    --chartreuse: #93ae2c;
    --paper: #ecedeb;
    --ink-light: #e9ecef;
    --ink-muted: #aeb6c0;
    --ink-gray: #6f747a;
    --backdrop: #d9d6d0;
  }
  * { box-sizing: border-box; margin: 0; padding: 0; }
  html, body { width: 1200px; height: 1000px; overflow: hidden; }
  body {
    background: var(--backdrop);
    font-family: "Ubuntu", sans-serif;
    font-weight: 300;
    display: flex;
    flex-direction: column;
    align-items: center;
    justify-content: center;
    gap: 60px;
  }
  .card {
    position: relative;
    width: 700px;
    height: 400px;
    overflow: hidden;
    box-shadow: 0 6px 18px rgba(0,0,0,.18);
  }
  .card-art { position: absolute; inset: 0; }

  /* Brand card */
  .card--brand { background: var(--charcoal); }
  .brand {
    position: absolute;
    left: 0; right: 0; top: 120px;
    text-align: center;
    color: var(--ink-light);
  }
  .brand-name {
    display: inline-flex;
    align-items: center;
    gap: 12px;
    font-size: 30px;
    font-weight: 300;
    letter-spacing: 1px;
    text-transform: uppercase;
  }
  .brand-mark { width: 16px; height: 16px; background: var(--chartreuse); }
  .brand-tagline { font-size: 18px; margin-top: 6px; color: var(--ink-muted); }

  /* Contact card */
  .card--contact { background: var(--charcoal); }
  .card--contact .brand { left: 20px; right: auto; width: 280px; top: 160px; color: var(--ink-gray); }
  .card--contact .brand-name { font-size: 23px; gap: 10px; }
  .card--contact .brand-tagline { color: var(--ink-gray); font-size: 16px; }

  .contact {
    position: absolute;
    left: 420px; top: 70px;
    color: var(--ink-light);
  }
  .contact-name { font-size: 28px; font-weight: 400; letter-spacing: .5px; white-space: nowrap; }
  .contact-title { font-size: 14px; color: var(--ink-muted); margin-top: 4px; }
  .contact-list { list-style: none; margin-top: 22px; font-size: 13px; line-height: 1.65; color: var(--ink-light); }
  .contact-list li { display: flex; align-items: flex-start; gap: 8px; white-space: nowrap; }
  .contact-list svg { width: 12px; height: 12px; margin-top: 4px; flex: none; fill: var(--chartreuse); }
  .contact-list .showroom { color: var(--chartreuse); }
  .contact-list .indent { padding-left: 20px; }
</style>
</head>
<body>

  <section class="card card--brand" aria-label="Business card front">
    <svg class="card-art" viewBox="0 0 700 400" preserveAspectRatio="none" aria-hidden="true">
      <path d="M0 400 L0 372 C250 330 480 270 700 160 L700 198 C480 305 250 360 0 400 Z" fill="var(--chartreuse)"/>
      <path d="M0 400 C250 360 480 305 700 198 L700 400 Z" fill="var(--charcoal-soft)"/>
    </svg>
    <div class="brand">
      <div class="brand-name"><span class="brand-mark"></span>Vantorel Stone</div>
      <div class="brand-tagline">Design Studio</div>
    </div>
  </section>

  <section class="card card--contact" aria-label="Business card back">
    <svg class="card-art" viewBox="0 0 700 400" preserveAspectRatio="none" aria-hidden="true">
      <polygon points="0,0 384,0 324,400 0,400" fill="var(--chartreuse)"/>
      <polygon points="0,0 360,0 300,400 0,400" fill="var(--paper)"/>
    </svg>
    <div class="brand">
      <div class="brand-name"><span class="brand-mark"></span>Vantorel Stone</div>
      <div class="brand-tagline">Design Studio</div>
    </div>
    <div class="contact">
      <h1 class="contact-name">Marisol T. Quenby</h1>
      <p class="contact-title">President &amp; Marketing Director</p>
      <ul class="contact-list">
        <li><svg viewBox="0 0 12 12"><path d="M2 0h3l1 3-2 1a7 7 0 0 0 4 4l1-2 3 1v3a2 2 0 0 1-2 2A10 10 0 0 1 0 2a2 2 0 0 1 2-2z"/></svg>602-418-5093</li>
        <li><svg viewBox="0 0 12 12"><rect x="3" y="0" width="6" height="4"/><rect x="0" y="5" width="12" height="5" rx="1"/><rect x="3" y="9" width="6" height="3"/></svg>602-731-6624</li>
        <li><svg viewBox="0 0 12 12"><path d="M0 2h12v8H0z M0 2l6 5 6-5"/></svg>marisol@vantorelstone.example</li>
        <li><svg viewBox="0 0 12 12"><path d="M6 0a4 4 0 0 1 4 4c0 3-4 8-4 8S2 7 2 4a4 4 0 0 1 4-4z"/></svg><span class="showroom">Vantorel Stone Showroom</span></li>
        <li class="indent">“Quillmont Design Center” 4183 W</li>
        <li class="indent">Palomar, Scottsdale AZ</li>
      </ul>
    </div>
  </section>

</body>
</html>
```